Local Roofing/Construction company business needs new biz card design

We need a new business card design, current cards are from the start of this operation and generic at best. We are a local Construction Company (General Contractor) with a majority of our work originating from insurance claims-exterior finish work is the main focus (Roofs-Siding-Gutters etc). Heavily involved with homeowners and the low ball offers they receive from insurance company's after a insurable event takes place. I have attached some of our original logo file(s) below.

```html
<!DOCTYPE html>
<html lang="en">
<head>
<meta charset="utf-8">
<title>Stonegate Construction – Business Card</title>
<link href="https://fonts.googleapis.com/css2?family=Montserrat:wght@400;700;800&display=swap" rel="stylesheet">
<style>
  :root {
    --backdrop: #3b3431;
    --card-dark: #172022;
    --card-mid: #22302f;
    --brand-green: #3fa656;
    --brand-green-light: #4cbf63;
    --text-light: #dfe4e2;
    --text-muted: #b9c2bf;
  }
  * { margin: 0; padding: 0; box-sizing: border-box; }
  html, body { width: 1200px; height: 716px; overflow: hidden; }
  body {
    background: var(--backdrop);
    font-family: "Montserrat", Arial, sans-serif;
    position: relative;
  }
  .card {
    position: absolute;
    top: 209px;
    width: 520px;
    height: 297px;
    border-radius: 3px;
    box-shadow: 0 14px 30px rgba(0,0,0,0.45);
    overflow: hidden;
  }
  .card--back { left: 60px; border-bottom: 6px solid var(--brand-green); }
  .card--front {
    left: 620px;
    background: linear-gradient(135deg, var(--card-mid) 0%, var(--card-dark) 60%);
    color: var(--text-light);
  }
  .back-pattern {
    position: absolute; inset: 0;
    background: radial-gradient(circle at 80% 30%, #2b3a3a 0%, #1a2324 55%, #131a1b 100%);
  }
  .back-mark {
    position: absolute; right: 54px; bottom: 40px;
    display: flex; align-items: center; gap: 6px;
    font-weight: 700; font-size: 9px; letter-spacing: 0.06em;
    color: var(--brand-green-light); text-transform: uppercase;
  }
  .back-mark .square { width: 10px; height: 10px; background: var(--brand-green); }

  .brand {
    position: absolute; top: 52px; right: 40px;
    display: flex; align-items: center; gap: 10px;
  }
  .brand .square { width: 28px; height: 28px; background: var(--brand-green); border-radius: 3px; }
  .brand-name {
    font-weight: 800; font-size: 24px; line-height: 1.05;
    letter-spacing: 0.02em; color: var(--brand-green-light); text-transform: uppercase;
  }
  .identity {
    position: absolute; top: 142px; right: 242px; text-align: right;
  }
  .identity .name {
    font-weight: 700; font-size: 17px; letter-spacing: 0.04em;
    color: var(--brand-green-light); text-transform: uppercase;
  }
  .identity .role { font-size: 11px; color: var(--text-muted); margin-top: 3px; }
  .divider {
    position: absolute; top: 142px; left: 292px;
    width: 1.5px; height: 62px; background: var(--brand-green);
  }
  .contacts {
    position: absolute; top: 144px; left: 306px;
    list-style: none; font-size: 11.5px; line-height: 20px;
  }
  .contacts li { display: flex; align-items: center; gap: 6px; }
  .contacts svg { width: 10px; height: 10px; fill: var(--brand-green-light); flex: none; }
  .address {
    position: absolute; top: 222px; left: 40px;
    font-size: 11.5px; color: var(--text-light);
  }
</style>
</head>
<body>
  <section class="card card--back">
    <div class="back-pattern" role="img" aria-label="Repeating faint brand-mark pattern on dark slate background"></div>
    <div class="back-mark"><span class="square"></span>Stonegate</div>
  </section>

  <section class="card card--front">
    <div class="brand">
      <span class="square"></span>
      <div class="brand-name">Stonegate<br>Construction</div>
    </div>

    <div class="identity">
      <p class="name">Dale Morrow</p>
      <p class="role">Managing Director</p>
    </div>
    <div class="divider"></div>

    <ul class="contacts">
      <li>
        <svg viewBox="0 0 10 10" aria-hidden="true"><path d="M2 0.5 L3.6 2.6 L2.8 3.6 Q4 6 6.4 7.2 L7.4 6.4 L9.5 8 L8.4 9.5 Q4 9.4 0.5 1.6 Z"/></svg>
        0400 512 736
      </li>
      <li>
        <svg viewBox="0 0 10 10" aria-hidden="true"><path d="M0.5 2 H9.5 V8.5 H0.5 Z M0.5 2 L5 5.5 L9.5 2" stroke="#172022" stroke-width="0.8"/></svg>
        info@stonegatebuild.com
      </li>
      <li>
        <svg viewBox="0 0 10 10" aria-hidden="true"><circle cx="5" cy="5" r="4.5"/></svg>
        www.stonegatebuild.com
      </li>
    </ul>

    <p class="address">1450 W Harmon Street Clearwater County 4820</p>
  </section>
</body>
</html>
```